Copper Lantern

Need a business card for our restaurant. Restaurant and Bar in the mountains of North Idaho. Rustic looking card

rustic design, wood and metal looking, primarily neutral colors

• Name, address, phone number, website, email address

```html
<!DOCTYPE html>
<html lang="en">
<head>
<meta charset="utf-8">
<title>Copper Lantern – Business Card</title>
<link rel="stylesheet" href="https://fonts.googleapis.com/css2?family=Lato:wght@400;700&family=Permanent+Marker&display=swap">
<style>
  :root {
    --stage-light: #5c5c5c;
    --stage-dark: #2e2e2e;
    --card-dark: #1f1f1f;
    --card-light: #d6d6d6;
    --ink: #1e1e1e;
    --silver: #c9c9c9;
  }
  * { margin: 0; padding: 0; box-sizing: border-box; }
  html, body { width: 1047px; height: 1200px; overflow: hidden; }
  body {
    background: radial-gradient(ellipse at 50% 48%, var(--stage-light) 0%, var(--stage-dark) 100%);
    position: relative;
    font-family: "Lato", sans-serif;
  }
  .card {
    position: absolute;
    left: 156px;
    width: 743px;
    height: 423px;
    border-radius: 16px;
    overflow: hidden;
    background: var(--card-dark);
  }
  .card--front { top: 120px; }
  .card--back { top: 634px; }
  .card__wave { position: absolute; inset: 0; }
  .brand-mark {
    position: absolute;
    left: 469px;
    top: 150px;
    width: 200px;
    text-align: center;
    color: var(--card-light);
    font-family: "Lato", sans-serif;
    font-weight: 700;
    font-size: 26px;
    letter-spacing: 2px;
    text-transform: uppercase;
    line-height: 1.2;
  }
  .person {
    position: absolute;
    left: 47px;
    top: 216px;
    color: var(--ink);
  }
  .person__name {
    font-family: "Permanent Marker", cursive;
    font-size: 29px;
    letter-spacing: 1px;
    line-height: 1;
  }
  .person__role {
    font-size: 18px;
    margin-top: 9px;
  }
  .contact {
    position: absolute;
    left: 49px;
    top: 300px;
    list-style: none;
    color: var(--ink);
    font-size: 16px;
  }
  .contact__item {
    display: flex;
    align-items: center;
    height: 26px;
  }
  .contact__icon { width: 14px; height: 14px; margin-right: 12px; fill: var(--ink); }
  .pattern-field {
    position: absolute;
    inset: 14px;
    border-radius: 6px;
    background: linear-gradient(90deg, #b8b8b8 0%, #6a6a6a 35%, #2c2c2c 60%, #0c0c0c 100%);
    opacity: 0.55;
  }
</style>
</head>
<body>
  <section class="card card--front" aria-label="Business card front">
    <svg class="card__wave" viewBox="0 0 743 423" aria-hidden="true">
      <path d="M0 160 C 120 120, 280 130, 390 245 C 480 335, 600 385, 743 340 L743 423 L0 423 Z" fill="var(--card-light)"/>
      <path d="M0 171 C 120 131, 280 141, 390 256 C 480 346, 600 396, 743 351" fill="none" stroke="var(--card-dark)" stroke-width="5"/>
    </svg>

    <div class="brand-mark">Copper<br>Lantern</div>

    <div class="person">
      <h1 class="person__name">DALE MERCER</h1>
      <p class="person__role">Founder &amp; CEO</p>
    </div>

    <ul class="contact">
      <li class="contact__item">
        <svg class="contact__icon" viewBox="0 0 24 24"><path d="M6.6 10.8a15.1 15.1 0 0 0 6.6 6.6l2.2-2.2c.3-.3.7-.4 1-.2 1.1.4 2.3.6 3.6.6.6 0 1 .4 1 1V20c0 .6-.4 1-1 1C10.6 21 3 13.4 3 4c0-.6.4-1 1-1h3.5c.6 0 1 .4 1 1 0 1.3.2 2.5.6 3.6.1.3 0 .7-.2 1z"/></svg>
        (208) 555-0147
      </li>
      <li class="contact__item">
        <svg class="contact__icon" viewBox="0 0 24 24"><path d="M2 5h20v14H2z M2 5l10 7 10-7" stroke="#d6d6d6" stroke-width="1.5"/></svg>
        info@copperlanternwallace.com
      </li>
      <li class="contact__item">
        <svg class="contact__icon" viewBox="0 0 24 24"><circle cx="12" cy="12" r="10"/><path d="M2 12h20M12 2c3 3 3 17 0 20M12 2c-3 3-3 17 0 20" stroke="#d6d6d6" stroke-width="1.5" fill="none"/></svg>
        copperlanternwallace.com
      </li>
      <li class="contact__item">
        <svg class="contact__icon" viewBox="0 0 24 24"><path d="M12 2a7 7 0 0 0-7 7c0 5 7 13 7 13s7-8 7-13a7 7 0 0 0-7-7zm0 9.5A2.5 2.5 0 1 1 12 6.5a2.5 2.5 0 0 1 0 5z"/></svg>
        412 Ridge St, Wallace, ID 83873
      </li>
    </ul>
  </section>

  <section class="card card--back" aria-label="Business card back">
    <div class="pattern-field" role="img" aria-label="Repeating brand emblem pattern fading from silver to black"></div>
  </section>
</body>
</html>
```